Book Title: “Faith: Road of Endless Grace” Please see the attachment “Text on the cover”.

Book Cover Design Instructions: This book is meant for people of all religions and nationalities. Therefore, on the cover, there should be no mosque or an object specific to any religion. The primary emphasis should be on the "unconditional love of God." Therefore, use universal symbols of love. The second priority themes could be Sufism, Peace, and self-improvement. Rest is your imagination. Please also see the attachment: 'Book description and author's Bio.'
This book has the potential to be a best seller. Please do a good job.
What Book Cover Formats are required: A designer should submit cover designs in three formats: (1) eBook, (2) Paperback, and (3) Hardback. These books will be published on Borvex QPL.
Format requirements for eBooks are available from: https://qpl.borvex.example/en_US/help/topic/R731928457.
You can find paperback and hardback cover measurements from: https://qpl.borvex.example/en_US/cover-calculator
• To complete the project, all three formats should be accepted by Borvex QPL.
• The book interior trim size is 6.14 X 9.21 inches.
• Interior Type: Premium color.
• No bleed.
• I do not upload barcode. So, the back cover should have room for Borvex to print the barcode.
• Number of pages 126.
Compensation for the designer: After selecting one designer, I will increase the amount by $200 on Artvelle to compensate for three deliverables.
Follow-up of the Project:
After the book is published, I may need minor revisions. For example, the number of pages may change. Therefore, I will need the same design in revised sizes. In that case, I will pay $25 for each revision. For example, if the number of pages changes, I will need a different spine for paperback and hardback, then I will pay the artist $25 + $25 = $50 for both designs.
List of Enclosers:
1. Text on the cover.
2. Book description and author's Bio for the back cover.
3. Later, I will upload my picture for the book's back cover.

Target Market(s)

Any adult

Industry/Entity Type

Any industry

Requirements
Must have
• Three Deliverables

```html
<!DOCTYPE html>
<html lang="en">
<head>
<meta charset="utf-8">
<title>Faith: Road of Endless Grace — Cover Wrap</title>
<link href="https://fonts.googleapis.com/css2?family=Cinzel:wght@500;600;700&family=Montserrat:wght@400;500&display=swap" rel="stylesheet">
<style>
  :root{
    --bg:#000;
    --gold:#a87f3a;
    --gold-light:#e8cd86;
    --gold-deep:#8a6326;
    --ink:#1e1e22;
    --sky-top:#b7d6ea;
    --sky-mid:#c9d8e6;
    --sky-low:#e7ecf1;
    --front-top:#8fc3dc;
    --front-glow:#fff8de;
  }
  *{margin:0;padding:0;box-sizing:border-box}
  html,body{width:1200px;height:1200px;overflow:hidden;background:var(--bg)}
  .canvas{position:relative;width:1200px;height:1200px;background:var(--bg)}
  .wrap{position:absolute;left:49px;top:205px;width:1102px;height:791px}

  .back-cover{position:absolute;left:0;top:0;width:531px;height:791px;overflow:hidden}
  .back-sky{position:absolute;inset:0;
    background:
      radial-gradient(ellipse 60% 30% at 30% 95%, rgba(255,255,255,.9), transparent 70%),
      radial-gradient(ellipse 40% 20% at 90% 75%, rgba(255,255,255,.6), transparent 70%),
      linear-gradient(180deg,var(--sky-top) 0%,var(--sky-mid) 55%,var(--sky-low) 100%)}
  .back-content{position:absolute;left:34px;top:36px;width:463px;color:var(--ink)}
  .back-title{font-family:"Cinzel",serif;font-weight:600;font-size:25.5px;color:var(--gold);letter-spacing:.6px;white-space:nowrap}
  .back-subtitle{font-family:"Cinzel",serif;font-weight:600;font-size:12.6px;color:var(--gold);margin-top:10px;letter-spacing:.2px;white-space:nowrap}
  .blurb{font-family:"Montserrat",sans-serif;font-size:11.2px;line-height:12.7px;text-align:justify;margin-top:4px}
  .blurb p{margin-bottom:12.7px}
  .author-photo{position:absolute;left:33px;top:546px;width:135px;height:169px;background:#fff;border:1px solid var(--gold)}
  .author-block{position:absolute;left:184px;top:546px;width:313px}
  .author-name{font-family:"Cinzel",serif;font-weight:600;font-size:20px;color:var(--gold);letter-spacing:.6px}
  .author-bio{font-family:"Montserrat",sans-serif;font-size:11.2px;line-height:12.7px;text-align:justify;margin-top:6px;color:var(--ink)}
  .barcode-space{position:absolute;left:306px;top:658px;width:193px;height:103px;background:#fff;border:1px solid var(--gold)}

  .spine{position:absolute;left:531px;top:0;width:40px;height:791px;
    background:linear-gradient(90deg,var(--gold-deep),var(--gold-light) 45%,#c9a25a 70%,var(--gold-deep))}
  .spine-text{position:absolute;left:40px;top:38px;transform-origin:0 0;transform:rotate(90deg);
    width:715px;display:flex;justify-content:space-between;height:40px;align-items:center;
    font-family:"Cinzel",serif;font-weight:600;color:var(--gold-deep);letter-spacing:.5px;white-space:nowrap}
  .spine-title{font-size:24px}
  .spine-author{font-size:19px}

  .front-cover{position:absolute;left:571px;top:0;width:531px;height:791px;overflow:hidden}
  .front-sky{position:absolute;inset:0;
    background:
      radial-gradient(circle at 50% 33%, var(--front-glow) 0%, rgba(255,244,210,.85) 8%, rgba(230,235,225,.4) 30%, transparent 55%),
      radial-gradient(ellipse 90% 35% at 50% 100%, rgba(255,255,255,.85), transparent 70%),
      linear-gradient(180deg,var(--front-top) 0%,#b2d2df 45%,#c8dbe4 75%,#e6ecef 100%)}
  .front-title{position:absolute;left:0;right:0;top:30px;text-align:center;font-family:"Cinzel",serif;font-weight:700;
    background:linear-gradient(180deg,var(--gold-light) 0%,var(--gold) 55%,var(--gold-deep) 100%);
    -webkit-background-clip:text;background-clip:text;color:transparent;line-height:1}
  .front-title .l1{display:block;font-size:106px}
  .front-title .l2{display:block;font-size:78px;margin-top:-14px}
  .front-title .l3{display:block;font-size:50px;margin-top:-4px}
  .front-subtitle{position:absolute;left:0;right:0;top:415px;text-align:center;font-family:"Cinzel",serif;font-weight:700;font-style:italic;
    font-size:25px;line-height:32px;color:var(--gold)}
  .front-band{position:absolute;left:0;bottom:0;width:531px;height:74px;
    background:linear-gradient(180deg,var(--gold-light),#c9a25a 50%,var(--gold-deep));
    display:flex;align-items:center;justify-content:center}
  .front-author{font-family:"Cinzel",serif;font-weight:600;font-size:27px;color:var(--gold-deep);letter-spacing:1px}
</style>
</head>
<body>
<div class="canvas">
  <div class="wrap">
    <section class="back-cover">
      <div class="back-sky" role="img" aria-label="Soft blue sky with white clouds"></div>
      <div class="back-content">
        <h2 class="back-title">FAITH: ROAD OF ENDLESS GRACE</h2>
        <h3 class="back-subtitle">A HANDBOOK FOR NURTURING CALM HEARTS AND KIND LIVING</h3>
        <div class="blurb">
          <p>This book gently weaves together the contemplative traditions of the mystics with timeless spiritual wisdom to offer a clear and caring map for inner growth. Readers are invited to taste for themselves the deep stillness and generous love that seekers of every land have treasured through the ages. Along the way it explores these central questions:</p>
          <p>How can we love the Divine without conditions? This is the highest form of love, one that opens a deep and life-changing inner journey.</p>
          <p>How can we sense the love of the Divine, which brings lasting calm and quiet joy?</p>
          <p>How can we accept and love ourselves, a practice that supports growth and balance?</p>
          <p>What is the wisest way to meet life's hardest moments so that pain eases and healing comes sooner?</p>
          <p>The book also looks closely at the duty to avoid harm and unfairness toward others, a theme that appears again and again across sacred writings. Refusing to wrong anyone in daily dealings is presented as the first task for every sincere seeker of the good.</p>
          <p>Great teachers did not merely speak of peace and kindness. They lived it, resolving conflict through patience and dialogue rather than force, and welcoming neighbors of many beliefs into one shared community. Their examples show how calm leadership can change the course of history without bloodshed.</p>
          <p>In the same spirit, the book recalls agreements made with bitter rivals, where patient restraint brought long and costly quarrels to a quiet and lasting close for all involved.</p>
          <p>Above all, the book sets out a step-by-step practice for reaching a settled, grateful and contented soul, the serene state that every traveler on the inner road hopes to find at last.</p>
        </div>
      </div>
      <div class="author-photo" role="img" aria-label="Space for the author portrait"></div>
      <div class="author-block">
        <h3 class="author-name">DR. RAVEL OSTRAND</h3>
        <p class="author-bio">Dr. Ostrand first trained as an engineer and later turned to the study of world spiritual traditions. He earned his doctorate in comparative religion and has spent many years teaching quiet reflection and kindness.</p>
      </div>
      <div class="barcode-space" aria-label="Reserved space for printer barcode"></div>
    </section>

    <section class="spine">
      <div class="spine-text">
        <span class="spine-title">FAITH: ROAD OF ENDLESS GRACE</span>
        <span class="spine-author">DR. RAVEL OSTRAND</span>
      </div>
    </section>

    <section class="front-cover">
      <div class="front-sky" role="img" aria-label="Radiant sun breaking through heavenly clouds with sparkling stars"></div>
      <h1 class="front-title">
        <span class="l1">FAITH:</span>
        <span class="l2">ROAD OF</span>
        <span class="l3">ENDLESS GRACE</span>
      </h1>
      <p class="front-subtitle">A Handbook for Nurturing<br>Calm Hearts and Kind Living</p>
      <div class="front-band"><span class="front-author">DR. RAVEL OSTRAND</span></div>
    </section>
  </div>
</div>
</body>
</html>
```